Flyer Design Project - Lantern Breathing

I require a flyer to be created for a course. It is a meditation course. So I want the cover design to look quirky but calm.

I have attached a previous design. This project is for lantern breathing. Although I have attached the previous flyer for guidance of the lay out and words used, I DO NOT want to to be a direct copy, I want it to look completely different. SO be creative. Any copies or anything that looks close to a copy will not even be considered.

I have also attached the wording for the back of the flyer in the attached word document.

I want the flyer to be A5 side but also the ability to resize it onto smaller cards.

If you need further information about the design brief please contact me.

Target Market(s)

20 to 30 male and female

Requirements
Must have
• Must have space for a logo which is currently being designed by the pixel harbor. For the time being insert the silver fern hollow wellness logo which is attached.

Picture something related to wine on the front and course detail on the back same as the attached sample.
Should not have
• a direct copy of my samples I have attached.

```html
<!DOCTYPE html>
<html lang="en">
<head>
<meta charset="utf-8">
<title>Lantern Breathing — Course Flyer</title>
<link rel="stylesheet" href="https://fonts.googleapis.com/css2?family=Roboto+Slab:wght@900&family=Josefin+Sans:wght@300&display=swap">
<style>
  :root {
    --backdrop-light: #fbfaf8;
    --backdrop-mid: #ecebe8;
    --backdrop-edge: #c9c7c3;
    --ink-navy: #1a2a3a;
    --wine-deep: #4a1526;
    --wine-mid: #7d2639;
    --wine-glow: #b8576a;
    --rule-soft: #b9b6b1;
  }
  html, body {
    margin: 0;
    padding: 0;
    width: 1200px;
    height: 846px;
    overflow: hidden;
  }
  .flyer {
    position: relative;
    width: 1200px;
    height: 846px;
    overflow: hidden;
    background: radial-gradient(ellipse 70% 80% at 30% 40%, var(--backdrop-light) 0%, var(--backdrop-mid) 60%, var(--backdrop-edge) 100%);
  }
  .hero-photo {
    position: absolute;
    right: 70px;
    top: 70px;
    width: 440px;
    height: 706px;
    border-radius: 220px 220px 24px 24px;
    background: radial-gradient(ellipse 65% 55% at 50% 40%, var(--wine-glow) 0%, var(--wine-mid) 45%, var(--wine-deep) 100%);
  }
  .title-block {
    position: absolute;
    left: 90px;
    top: 250px;
    width: 560px;
  }
  .title-rule {
    width: 120px;
    height: 4px;
    background: var(--ink-navy);
    margin-bottom: 34px;
  }
  .course-title {
    margin: 0;
    color: var(--ink-navy);
    line-height: 1.05;
  }
  .course-title .title-strong {
    display: block;
    font-family: "Roboto Slab", Georgia, serif;
    font-weight: 900;
    font-size: 88px;
    letter-spacing: 1px;
  }
  .course-title .title-light {
    display: block;
    font-family: "Josefin Sans", Arial, sans-serif;
    font-weight: 300;
    font-size: 84px;
    letter-spacing: 3px;
    margin-top: 6px;
  }
  .logo-slot {
    position: absolute;
    left: 90px;
    bottom: 80px;
    display: flex;
    align-items: center;
    gap: 16px;
    padding-top: 22px;
    border-top: 1px solid var(--rule-soft);
    width: 480px;
  }
  .logo-dot {
    width: 34px;
    height: 34px;
    border-radius: 50%;
    background: var(--ink-navy);
    flex: none;
  }
  .logo-name {
    font-family: "Josefin Sans", Arial, sans-serif;
    font-weight: 300;
    font-size: 24px;
    letter-spacing: 2px;
    color: var(--ink-navy);
    text-transform: uppercase;
    white-space: nowrap;
  }
</style>
</head>
<body>
  <main class="flyer">
    <div class="hero-photo" role="img" aria-label="Photograph of a calm person meditating beside a glass of red wine"></div>
    <div class="title-block">
      <div class="title-rule"></div>
      <h1 class="course-title"><span class="title-strong">LANTERN</span><span class="title-light">BREATHING</span></h1>
    </div>
    <div class="logo-slot">
      <span class="logo-dot"></span>
      <span class="logo-name">Silver Fern Hollow Wellness</span>
    </div>
  </main>
</body>
</html>
```